NEW Modern Sleek Business Card for VR Language Startup

Our startup is using VR to lead the next wave of world language education. We need a two-sided business card that introduces the larger organization (Brightloom Language Inc) and our contact info on one side and shows the product, Glimwoorld, on the other side.

Side 1 (contact info)= Brightloom Logo and Contact info (name, title, phone, email)

Side 2 (product)= Glimworld logo, text, and website
Text= Culturally Immersive Language Learning Games
Website= www.glimworld-play.com

Target Market(s)

Education, Technology

Contact Information for Business Card

Contact info will be updated upon approval of the design. For now, put this as a placeholder.

Perry Dunmore
Founder & CEO
pdunmore@quillpost-mail.net
(555)-014-2286

Font styles to use
Other font styles liked:
• Gibson and Century Gothic are the brand fonts

Requirements
Nice to have
• I would love to see cohesion between the design and colors of the two logos. I have attached a few business card designs that I like, so you can get a feel for my preferred style.

```html
<!DOCTYPE html>
<html lang="en">
<head>
<meta charset="utf-8">
<title>Brightloom Language &amp; Glimworld Business Cards</title>
<link rel="stylesheet" href="https://fonts.googleapis.com/css2?family=Lato:wght@400;700&display=swap">
<style>
  :root {
    --backdrop: #2a2a2a;
    --card: #ffffff;
    --ink: #2b2b2b;
    --ink-strong: #1c1c1c;
    --rule: #3a3a3a;
    --warm-start: #f4a93a;
    --warm-end: #fb5a3c;
    --name-start: #f26a3d;
    --name-end: #7a5cf0;
    --cool-start: #1fe4e6;
    --cool-end: #3d9cf3;
    --link: #1aa3e8;
    --brand-dot-warm: #f46d3e;
    --brand-dot-cool: #2fb6ef;
  }
  * { box-sizing: border-box; margin: 0; padding: 0; }
  html, body {
    width: 1200px;
    height: 1200px;
    overflow: hidden;
    background: var(--backdrop);
    font-family: "Lato", Arial, sans-serif;
  }
  .canvas {
    position: relative;
    width: 1200px;
    height: 1200px;
  }
  .card {
    position: absolute;
    top: 310px;
    width: 366px;
    height: 594px;
    background: var(--card);
    overflow: hidden;
    text-align: center;
  }
  .card--contact { left: 233px; }
  .card--product { left: 627px; width: 369px; }

  .brand {
    position: absolute;
    left: 0;
    right: 0;
    display: flex;
    align-items: center;
    justify-content: center;
    gap: 14px;
  }
  .brand__dot {
    width: 22px;
    height: 22px;
    border-radius: 50%;
    flex: none;
  }
  .brand__name {
    font-weight: 700;
    color: var(--ink-strong);
    line-height: 1;
  }
  .card--contact .brand { top: 196px; }
  .card--contact .brand__dot { background: var(--brand-dot-warm); }
  .card--contact .brand__name {
    font-size: 30px;
    letter-spacing: 3px;
    text-transform: uppercase;
  }
  .card--product .brand { top: 238px; }
  .card--product .brand__dot { background: var(--brand-dot-cool); }
  .card--product .brand__name {
    font-size: 46px;
    color: #3b3b3b;
  }

  .contact {
    position: absolute;
    top: 322px;
    left: 0;
    right: 0;
  }
  .contact__name {
    font-size: 23px;
    font-weight: 400;
    text-transform: uppercase;
    letter-spacing: 0.2px;
    background: linear-gradient(90deg, var(--name-start), var(--name-end));
    -webkit-background-clip: text;
    background-clip: text;
    color: transparent;
    line-height: 1;
  }
  .contact__title {
    font-size: 17px;
    color: var(--ink);
    margin-top: 3px;
  }
  .contact__rule {
    width: 143px;
    height: 1px;
    background: var(--rule);
    margin: 10px auto 9px;
  }
  .contact__line {
    font-size: 16px;
    color: var(--ink);
    line-height: 23px;
  }

  .product-copy {
    position: absolute;
    top: 320px;
    left: 0;
    right: 0;
  }
  .product-copy__tagline {
    font-size: 17px;
    color: var(--ink);
    text-transform: uppercase;
    line-height: 22px;
  }
  .product-copy__url {
    display: block;
    margin-top: 9px;
    font-size: 18px;
    color: var(--link);
    text-decoration: none;
  }

  .accent-band {
    position: absolute;
    left: 0;
    right: 0;
    bottom: 0;
  }
  .card--contact .accent-band {
    height: 118px;
    background: linear-gradient(180deg, var(--warm-start), var(--warm-end));
  }
  .card--product .accent-band {
    height: 150px;
    background: linear-gradient(120deg, var(--cool-start), var(--cool-end));
  }
</style>
</head>
<body>
<main class="canvas">

  <section class="card card--contact" aria-label="Brightloom Language contact card">
    <div class="brand">
      <span class="brand__dot"></span>
      <span class="brand__name">Brightloom</span>
    </div>
    <div class="contact">
      <p class="contact__name">Perry Dunmore</p>
      <p class="contact__title">Founder &amp; CEO</p>
      <div class="contact__rule"></div>
      <p class="contact__line">(555)-014-2286</p>
      <p class="contact__line">pdunmore@quillpost-mail.net</p>
    </div>
    <div class="accent-band"></div>
  </section>

  <section class="card card--product" aria-label="Glimworld product card">
    <div class="brand">
      <span class="brand__dot"></span>
      <span class="brand__name">Glimworld</span>
    </div>
    <div class="product-copy">
      <p class="product-copy__tagline">Culturally Immersive<br>Language Learning Games</p>
      <a class="product-copy__url" href="#">www.glimworld-play.com</a>
    </div>
    <div class="accent-band"></div>
  </section>

</main>
</body>
</html>
```